Fun relaxed Travel Photography Business Card*

Require a fun, funky and quirky but rememberable business card for a travel photographer

Industry/Entity Type

Photographer

Contact Information for Business Card

Front Card

(my name) Lenn D.

Travel Photographer ( small under travel photographer) “self-proclaimed”

(website logo) wanderingsoflenn.net

(Instagram logo) @wanderings_of_lenn

(Instagram logo) @wanderings_of_lenn_2.0 (backup for when Instagram puts Lenn on timeout for bad behaviour)

Tel: N/A (removing the potential awkwardness of me not replying)

Email: (see above)

Back Card

Offending people since 1986

(Bottom right corner) “p.s. travelling made me fatTER”

Font styles to use
Serif

Colors

Designer to choose colors to be used in the design.

Requirements
Must have
• a camera
• a similar cartoon version of me as the "logo" see attached files, try to make as similar as possible

```html
<!DOCTYPE html>
<html lang="en">
<head>
<meta charset="utf-8">
<title>Lenn D. – Travel Photographer Business Card</title>
<link href="https://fonts.googleapis.com/css2?family=Montserrat:wght@400;500;600&family=Righteous&display=swap" rel="stylesheet">
<style>
  :root {
    --page-bg: #eceff1;
    --card-dark: #1e1e1e;
    --card-dark-edge: #262626;
    --card-light: #ffffff;
    --card-light-edge: #dcdcdc;
    --ink-light: #ffffff;
    --ink-dark: #1c1c1c;
    --ink-muted: #666666;
    --accent: #e8541c;
    --bracket: #1a1a1a;
    --figure-skin: #5a3420;
    --figure-shirt: #2a3f7a;
    --figure-shorts: #d8cbb0;
  }
  * { margin: 0; padding: 0; box-sizing: border-box; }
  html, body {
    width: 1200px; height: 1200px; overflow: hidden;
    background: var(--page-bg);
    font-family: "Montserrat", Arial, sans-serif;
  }
  .canvas { position: relative; width: 1200px; height: 1200px; }

  .card { position: absolute; left: 189px; width: 837px; height: 478px; }
  .card--back {
    top: 82px;
    background: linear-gradient(135deg, var(--card-dark-edge), var(--card-dark) 60%);
    color: var(--ink-light);
  }
  .card--front {
    top: 625px;
    background: linear-gradient(135deg, var(--card-light) 30%, var(--card-light-edge));
    color: var(--ink-dark);
  }

  /* back side */
  .brand {
    position: absolute; left: 0; right: 0; top: 200px;
    display: flex; align-items: center; justify-content: center; gap: 10px;
    font-size: 20px; font-weight: 500; letter-spacing: 0.5px;
  }
  .brand__dot { width: 12px; height: 12px; border-radius: 50%; background: var(--ink-light); }
  .tagline {
    position: absolute; left: 0; right: 0; top: 276px; text-align: center;
    font-family: "Righteous", "Trebuchet MS", sans-serif;
    font-size: 27px; letter-spacing: 1.2px; text-transform: uppercase;
  }
  .postscript {
    position: absolute; right: 46px; top: 410px;
    font-size: 19px; font-weight: 400;
  }
  .postscript strong { font-weight: 600; }

  /* front side */
  .bracket { position: absolute; width: 45px; height: 45px; border-color: var(--bracket); border-style: solid; }
  .bracket--top-right { left: 324px; top: 32px; border-width: 4px 4px 0 0; }
  .bracket--bottom-left { left: 178px; top: 399px; border-width: 0 0 4px 4px; }

  .avatar {
    position: absolute; left: 212px; top: 52px; width: 126px; height: 360px;
    border-radius: 60px 60px 20px 20px;
    background: linear-gradient(180deg, var(--figure-skin) 0 24%, var(--figure-shirt) 24% 64%, var(--figure-shorts) 64% 82%, var(--figure-skin) 82%);
  }

  .identity { position: absolute; left: 448px; top: 62px; }
  .identity__name { font-size: 32px; font-weight: 400; color: var(--accent); letter-spacing: 0.5px; line-height: 1.1; }
  .identity__role { font-size: 20px; font-weight: 500; letter-spacing: 0.4px; margin-top: 4px; }
  .identity__note { font-size: 15px; color: var(--ink-muted); letter-spacing: 0.4px; margin-top: 4px; }

  .contacts { position: absolute; left: 448px; top: 268px; list-style: none; }
  .contacts li { display: flex; align-items: center; gap: 11px; font-size: 20px; margin-bottom: 8px; line-height: 25px; }
  .contacts__icon { flex: none; width: 27px; height: 27px; }
</style>
</head>
<body>
<main class="canvas">

  <section class="card card--back" aria-label="Card back">
    <div class="brand"><span class="brand__dot"></span><span>LENN D. Photography</span></div>
    <p class="tagline">Offending people since 1986</p>
    <p class="postscript">p.s. travelling made me fat<strong>TER</strong></p>
  </section>

  <section class="card card--front" aria-label="Card front">
    <span class="bracket bracket--top-right"></span>
    <span class="bracket bracket--bottom-left"></span>
    <div class="avatar" role="img" aria-label="Cartoon character of Lenn in sunglasses, floral shirt, shorts and sandals"></div>

    <div class="identity">
      <h1 class="identity__name">LENN D.</h1>
      <p class="identity__role">TRAVEL PHOTOGRAPHER</p>
      <p class="identity__note">(SELF-PROCLAIMED)</p>
    </div>

    <ul class="contacts">
      <li>
        <svg class="contacts__icon" viewBox="0 0 27 27" aria-hidden="true">
          <circle cx="13.5" cy="13.5" r="13.5" fill="var(--accent)"/>
          <g fill="none" stroke="#fff" stroke-width="1.4">
            <circle cx="13.5" cy="13.5" r="7"/>
            <ellipse cx="13.5" cy="13.5" rx="3" ry="7"/>
            <line x1="6.5" y1="13.5" x2="20.5" y2="13.5"/>
          </g>
        </svg>
        <span>wanderingsoflenn.net</span>
      </li>
      <li>
        <svg class="contacts__icon" viewBox="0 0 27 27" aria-hidden="true">
          <circle cx="13.5" cy="13.5" r="13.5" fill="var(--accent)"/>
        </svg>
        <span>@wanderings_of_lenn<br>@wanderings_of_lenn_2.0</span>
      </li>
      <li>
        <svg class="contacts__icon" viewBox="0 0 27 27" aria-hidden="true">
          <circle cx="13.5" cy="13.5" r="13.5" fill="var(--accent)"/>
          <path d="M9 7.5c1-.8 2-.6 2.5.3l1 2c.3.7 0 1.3-.6 1.7l-.6.4c.7 1.6 1.8 2.8 3.4 3.5l.4-.6c.4-.6 1.1-.8 1.7-.5l2 1c.9.5 1 1.5.2 2.5-1 1.2-2.6 1.3-4.4.3-2.9-1.6-4.9-3.7-6.3-6.5-.8-1.8-.4-3.2.7-4.1z" fill="#fff"/>
        </svg>
        <span>N/A</span>
      </li>
      <li>
        <svg class="contacts__icon" viewBox="0 0 27 27" aria-hidden="true">
          <circle cx="13.5" cy="13.5" r="13.5" fill="var(--accent)"/>
          <rect x="7" y="9" width="13" height="9" rx="1" fill="none" stroke="#fff" stroke-width="1.5"/>
          <path d="M7.5 9.5l6 5 6-5" fill="none" stroke="#fff" stroke-width="1.5"/>
        </svg>
        <span>N/A</span>
      </li>
    </ul>
  </section>

</main>
</body>
</html>
```